Wedding Videography Wordpress Website Theme

We need a modern and high-end website look for our wedding video and film business. We film weddings all over the United Kingdom and at European destinations so need something to reflect our work. The website should be visually stunning with images and videos being the focal point as this is what our services are.

The current website is www.brunolessway.com so you will be able to see our brand.

My Instagram is www.instagram.com/brunolesswayfilms so a new design should link in with this idea.

We need the following pages designed by the winning designer

1 - Homepage
2 - Films Index Page
3 - Testimonials
4 - Prices
5 - Reviews
6 - Meet Bruno (About)
7 - Contact
8 - Blog Index
9 - Blog Page

All pages must be consistent so have a similar style.

Pages on menu:
Meet Bruno
Videos
Packages
Testimionials
Journal (Blog)
Contact

We require a responsive look too. Over 90% of our visitors access the website via their mobile devices.

```html
<!DOCTYPE html>
<html lang="en">
<head>
<meta charset="utf-8">
<title>Bruno Lessway Wedding Films</title>
<link href="https://fonts.googleapis.com/css2?family=Outfit:wght@400;500;600;700&family=Arimo:ital,wght@0,400;0,700;1,400&display=swap" rel="stylesheet">
<style>
:root{
  --ink:#111111;
  --white:#ffffff;
  --muted:#6b6b6b;
  --line:#2a2a2a;
  --footer:#161616;
  --red:#e0141b;
  --hero-a:#1e241c;
  --hero-b:#3a4234;
  --card:rgba(238,238,238,.93);
}
*{box-sizing:border-box;margin:0;padding:0}
html,body{width:1200px;height:4743px;overflow:hidden;background:var(--white);color:var(--ink);font-family:"Arimo",Arial,sans-serif}
section,header,footer{position:relative;width:1200px;overflow:hidden}
.abs{position:absolute}
.heading{font-family:"Outfit",sans-serif;font-weight:700;color:var(--ink);text-transform:uppercase;letter-spacing:.5px}
.btn{position:absolute;display:flex;align-items:center;justify-content:center;border:2px solid var(--ink);font-family:"Arimo",sans-serif;font-weight:700;font-size:16px;color:var(--ink);background:transparent;text-transform:uppercase}
.photo{position:absolute}

/* hero */
.hero{height:639px;background:linear-gradient(180deg,#2a3128 0%,var(--hero-b) 45%,var(--hero-a) 100%)}
.brand{position:absolute;left:0;width:1200px;top:60px;text-align:center;color:var(--white)}
.brand-mark{width:34px;height:34px;border:2px solid var(--white);margin:0 auto 14px}
.brand-name{font-family:"Outfit",sans-serif;font-weight:500;font-size:21px;letter-spacing:6px}
.brand-sub{font-family:"Outfit",sans-serif;font-weight:500;font-size:10px;letter-spacing:6px;margin-top:4px}
.nav{position:absolute;top:158px;left:0;width:1200px;display:flex;justify-content:center;gap:0}
.nav a{color:var(--white);text-decoration:none;font-size:18px;padding:0 25px;position:relative;height:48px}
.nav a.active::after{content:"";position:absolute;left:13px;right:13px;top:46px;height:3px;background:var(--white)}
.nav-rule{position:absolute;top:206px;left:0;width:1200px;height:1px;background:rgba(255,255,255,.25)}
.hero-title{position:absolute;top:325px;width:1200px;text-align:center;color:var(--white);font-size:57px;line-height:68px;font-weight:600}
.play{position:absolute;left:579px;top:478px}

/* meet */
.meet{height:605px}
.meet-text{position:absolute;left:142px;top:85px;width:410px}
.meet-text h2{font-size:50px}
.meet-text p{margin-top:28px;font-size:13.5px;line-height:25.5px;color:#555;text-align:justify}

/* videos */
.videos{height:409px}
.arrow-tab{position:absolute;top:173px;width:34px;height:60px;background:var(--ink);display:flex;align-items:center;justify-content:center}

/* packages */
.packages{height:672px}
.center-title{position:absolute;width:1200px;text-align:center;font-size:50px}
.pkg{position:absolute;top:193px;width:298px;height:383px;border:2px solid var(--line);text-align:center}
.pkg h3{font-family:"Outfit",sans-serif;font-weight:600;font-size:14.5px;margin-top:34px;text-transform:uppercase}
.pkg .sub{font-family:"Outfit",sans-serif;font-weight:600;font-size:13px;line-height:14px;text-transform:uppercase}
.price{display:inline-block;background:var(--ink);color:var(--white);font-family:"Outfit",sans-serif;font-weight:600;font-size:22px;width:180px;height:40px;line-height:40px;margin-top:16px;text-transform:uppercase}
.pkg p{font-size:12.5px;line-height:21.5px;color:#666;margin:18px 36px 0;text-align:justify;text-align-last:center}
.pkg .btn{left:72px;bottom:36px;width:152px;height:52px}
.circle-arrow{position:absolute;width:46px;height:46px;border:1.5px solid #555;border-radius:50%;display:flex;align-items:center;justify-content:center;background:var(--white)}

/* testimonials */
.testimonials{height:653px;background:linear-gradient(100deg,#3a302b 0%,#5a4a40 40%,#7c7068 65%,#b9b4b3 100%)}
.quote-card{position:absolute;left:144px;top:73px;width:463px;height:506px;background:var(--card);padding:52px 38px 0}
.quote-card h2{font-size:50px;text-align:center}
.quote-card blockquote{margin-top:20px;font-style:italic;font-size:12.5px;line-height:23px;color:#555;text-align:justify;text-align-last:center}
.reviewer{position:absolute;left:114px;top:390px;display:flex;align-items:center;gap:12px}
.avatar{width:56px;height:56px;border-radius:50%;background:#3b3a36}
.reviewer strong{display:block;font-size:12.5px;text-transform:uppercase}
.reviewer span{font-size:12.5px;font-weight:700}
.quote-mark{position:absolute;right:22px;bottom:16px;font-family:"Outfit",sans-serif;font-size:150px;line-height:100px;height:70px;color:#b5b5b5;overflow:hidden}

/* journal */
.journal{height:806px}
.post{position:absolute;top:208px;width:447px;text-align:center}
.post-img{width:447px;height:385px}
.post-card{position:absolute;top:333px;left:24px;width:399px;height:90px;background:var(--white);padding-top:14px}
.post-card h3{font-family:"Arimo",sans-serif;font-size:18px;line-height:27px;font-weight:700}
.date-badge{position:absolute;top:256px;left:184px}
.post p{position:absolute;top:432px;left:60px;width:327px;font-size:12px;line-height:17px;color:#666}
.post .btn{left:148px;top:482px;width:152px;height:56px}

/* contact */
.contact{height:655px;background:linear-gradient(100deg,#1c1a18 0%,#5b4d43 30%,#3c3530 55%,#2a2622 100%)}
.contact-card{position:absolute;left:594px;top:76px;width:462px;height:506px;background:var(--card)}
.contact-card h2{text-align:center;font-size:50px;margin-top:46px}
.field{position:absolute;border:1.5px solid #333;background:var(--white);font-size:12px;color:#333;padding:20px 0 0 26px}
.contact-card .btn{left:156px;top:398px;width:152px;height:56px}

/* footer */
.site-footer{height:304px;background:var(--footer);color:var(--white)}
.footer-brand{position:absolute;left:140px;top:50px;width:380px;text-align:center}
.footer-brand .brand-mark{width:60px;height:60px;margin-bottom:24px}
.footer-brand .brand-name{font-size:34px;letter-spacing:9px}
.footer-brand .brand-sub{font-size:16px;letter-spacing:10px;margin-top:6px}
.footer-links{position:absolute;left:604px;top:52px;list-style:none}
.footer-links li{font-size:15px;line-height:36.5px}
.newsletter{position:absolute;left:812px;top:52px;width:242px}
.newsletter h4{font-weight:400;font-size:20px;text-transform:uppercase}
.nl-input{margin-top:24px;height:46px;border:1.5px solid #bbb;font-size:12px;padding:16px 0 0 18px}
.nl-btn{margin-top:10px;height:46px;background:var(--white);color:var(--ink);font-weight:700;font-size:16px;display:flex;align-items:center;justify-content:center}
.copy{margin-top:22px;font-size:11.5px;line-height:18px}
</style>
</head>
<body>

<header class="hero" role="img" aria-label="Aerial view of a country house surrounded by trees">
  <div class="brand">
    <div class="brand-mark"></div>
    <div class="brand-name">BRUNO LESSWAY</div>
    <div class="brand-sub">WEDDING FILMS</div>
  </div>
  <nav class="nav">
    <a class="active">Meet Bruno</a><a>Videos</a><a>Packages</a><a>Testimonials</a><a>Journal</a><a>Contact</a>
  </nav>
  <div class="nav-rule"></div>
  <h1 class="hero-title heading">North East and Yorkshire<br>Wedding Videographer</h1>
  <svg class="play" width="42" height="42" viewBox="0 0 42 42"><circle cx="21" cy="21" r="19" fill="none" stroke="#fff" stroke-width="3"/><path d="M16 12 L30 21 L16 30 Z" fill="#fff"/></svg>
</header>

<section class="meet">
  <div class="meet-text">
    <h2 class="heading">Meet Bruno</h2>
    <p>Thanks so much for exploring my website. I hope you've had a chance to watch some of the gorgeous wedding films and you've enjoyed seeing the kind of high-quality, professional wedding video you could expect too. Videomaking has been a passion since I was eight years old. From making family videos, I went on to study video at college and then at degree level. You could say it's second nature to me by now – I've been honing my filmmaking skills for years!When I'm not behind a camera, I love spending quality time with my two children (have you seen our family videos here?). We're usually on an adventure somewhere,</p>
  </div>
  <div class="btn" style="left:141px;top:446px;width:151px;height:57px">Read More</div>
  <div class="photo" role="img" aria-label="Groom smiling at his bride during the ceremony" style="left:600px;top:0;width:600px;height:598px;background:linear-gradient(120deg,#2e2c2a 0%,#6f625a 40%,#bdb5ad 70%,#e6e2dc 100%)"></div>
</section>

<section class="videos">
  <div class="photo" role="img" aria-label="Film still of a bride getting ready" style="left:0;top:0;width:596px;height:409px;background:linear-gradient(120deg,#c9c0b8 0%,#a9927f 45%,#6e5a4c 100%)"></div>
  <div class="photo" role="img" aria-label="Film still of wedding speeches at the top table" style="left:604px;top:0;width:596px;height:409px;background:linear-gradient(120deg,#e4e1dd 0%,#9b8f86 45%,#3a3431 100%)"></div>
  <svg class="abs" style="left:280px;top:186px" width="38" height="38" viewBox="0 0 38 38"><circle cx="19" cy="19" r="19" fill="var(--red)"/><path d="M15 11 L27 19 L15 27 Z" fill="#fff"/></svg>
  <svg class="abs" style="left:884px;top:186px" width="38" height="38" viewBox="0 0 38 38"><circle cx="19" cy="19" r="19" fill="var(--red)"/><path d="M15 11 L27 19 L15 27 Z" fill="#fff"/></svg>
  <div class="arrow-tab" style="left:0;border-radius:0 30px 30px 0"><svg width="20" height="16" viewBox="0 0 20 16"><path d="M2 8 H17 M11 2 L17 8 L11 14" stroke="#fff" stroke-width="2.5" fill="none"/></svg></div>
  <div class="arrow-tab" style="right:0;border-radius:30px 0 0 30px"><svg width="20" height="16" viewBox="0 0 20 16"><path d="M18 8 H3 M9 2 L3 8 L9 14" stroke="#fff" stroke-width="2.5" fill="none"/></svg></div>
</section>

<section class="packages">
  <h2 class="center-title heading" style="top:86px">Packages</h2>
  <div class="circle-arrow" style="left:63px;top:360px"><svg width="12" height="18" viewBox="0 0 12 18"><path d="M9 2 L3 9 L9 16" stroke="#444" stroke-width="2" fill="none"/></svg></div>
  <div class="circle-arrow" style="left:1090px;top:360px"><svg width="12" height="18" viewBox="0 0 12 18"><path d="M3 2 L9 9 L3 16" stroke="#444" stroke-width="2" fill="none"/></svg></div>

  <article class="pkg" style="left:144px">
    <h3>Signature Wedding Film</h3>
    <div class="price">From £1,500</div>
    <p>My signature package includes coverage from 2 hours before the ceremony to 15 minutes after the first dance (max 8.30pm). You will receive a highlights film of your wedding day featuring audio, plus the full ceremony and speeches filmed with 3 cameras.</p>
    <div class="btn">Read More</div>
  </article>
  <article class="pkg" style="left:451px">
    <h3>Gold Wedding Film</h3>
    <div class="price">From £1,800</div>
    <p>My signature package includes coverage from 2 hours before the ceremony to 15 minutes after the first dance (max 8.30pm). You will receive a highlights film of your wedding day featuring audio, plus the full ceremony and speeches filmed with 3 cameras.</p>
    <div class="btn">Read More</div>
  </article>
  <article class="pkg" style="left:758px">
    <h3 style="margin-top:30px;line-height:14px">Second Videographer Half Day</h3>
    <div class="sub">£300 / Full Day £400</div>
    <div class="price" style="margin-top:6px">Add Ons</div>
    <p>A second videographer is essential if you have a multi-site wedding such as a church ceremony. This also allows you to get more video footage from more elements of your day. This option is perfect if you are getting ready in different locations.</p>
    <div class="btn">Read More</div>
  </article>
</section>

<section class="testimonials" role="img" aria-label="Bride in a long veil holding a bouquet">
  <div class="quote-card">
    <h2 class="heading">Testimonials</h2>
    <blockquote>What can I say other than – INCREDIBLE!! We weren't going to get a videographer but are so glad we did. Bruno has captured the whole day in the most beautiful way, with a magical video, we both can't stop watching it! If anyone is unsure about a videographer we would highly recommend getting one! We cannot recommend Bruno and his team enough! They made us feel at ease and most of the time we didn't even realise they were there. We had our film back within 24hours of our wedding finishing!! Bruno we cannot thank you enough for what you have created for us!! THANK YOU.</blockquote>
    <div class="reviewer">
      <div class="avatar" role="img" aria-label="Couple portrait"></div>
      <div><strong>Hannah and Tom</strong><span>Ashgrove Hall, Yorkshire</span></div>
    </div>
    <div class="quote-mark">&ldquo;</div>
  </div>
</section>

<section class="journal">
  <h2 class="center-title heading" style="top:78px">Journal</h2>
  <div class="circle-arrow" style="left:63px;top:422px"><svg width="12" height="18" viewBox="0 0 12 18"><path d="M9 2 L3 9 L9 16" stroke="#444" stroke-width="2" fill="none"/></svg></div>
  <div class="circle-arrow" style="left:1090px;top:422px"><svg width="12" height="18" viewBox="0 0 12 18"><path d="M3 2 L9 9 L3 16" stroke="#444" stroke-width="2" fill="none"/></svg></div>

  <article class="post" style="left:144px">
    <div class="post-img" role="img" aria-label="Bride walking down the aisle towards the groom" style="background:linear-gradient(110deg,#3a3530 0%,#6d655d 45%,#b9b0a6 75%,#d9d2c8 100%)"></div>
    <svg class="date-badge" width="80" height="78" viewBox="0 0 80 78"><path d="M40 0 L80 78 H0 Z" fill="var(--ink)"/><text x="40" y="56" fill="#fff" font-family="Outfit,sans-serif" font-weight="600" font-size="22" text-anchor="middle">12</text><text x="40" y="70" fill="#fff" font-family="Arimo,sans-serif" font-size="10" text-anchor="middle">AUG</text></svg>
    <div class="post-card"><h3>Lucy and Sam – Millbrook Inn<br>Old Barn Wedding</h3></div>
    <p>Lucy and Sam's Millbrook Inn Wedding</p>
    <div class="btn">Read More</div>
  </article>
  <article class="post" style="left:609px">
    <div class="post-img" role="img" aria-label="Groom laughing with a young flower girl" style="background:linear-gradient(110deg,#e8e6e2 0%,#b7aea4 40%,#5a524b 75%,#2e2a27 100%)"></div>
    <svg class="date-badge" width="80" height="78" viewBox="0 0 80 78"><path d="M40 0 L80 78 H0 Z" fill="var(--ink)"/><text x="40" y="56" fill="#fff" font-family="Outfit,sans-serif" font-weight="600" font-size="22" text-anchor="middle">11</text><text x="40" y="70" fill="#fff" font-family="Arimo,sans-serif" font-size="10" text-anchor="middle">AUG</text></svg>
    <div class="post-card"><h3>Fenwick Hall Wedding In<br>Northumberland</h3></div>
    <p>Gorgeous wedding at the stunning and quirky Fenwick Hall in Northumberland.</p>
    <div class="btn">Read More</div>
  </article>
</section>

<section class="contact" role="img" aria-label="Smiling bride walking through a confetti shower">
  <div class="contact-card">
    <h2 class="heading">Contact</h2>
    <div class="field" style="left:34px;top:134px;width:191px;height:54px">Enter Name</div>
    <div class="field" style="left:237px;top:134px;width:191px;height:54px">Enter Email</div>
    <div class="field" style="left:34px;top:205px;width:191px;height:54px">Phone</div>
    <div class="field" style="left:237px;top:205px;width:191px;height:54px">Address</div>
    <div class="field" style="left:34px;top:276px;width:394px;height:86px">Message</div>
    <div class="btn">Submit</div>
  </div>
</section>

<footer class="site-footer">
  <div class="footer-brand">
    <div class="brand-mark"></div>
    <div class="brand-name">BRUNO LESSWAY</div>
    <div class="brand-sub">WEDDING FILMS</div>
  </div>
  <ul class="footer-links">
    <li>Meet Bruno</li><li>Videos</li><li>Packages</li><li>Testimonials</li><li>Journal</li><li>Contact</li>
  </ul>
  <div class="newsletter">
    <h4>Sign Up Newsletter</h4>
    <div class="nl-input">Enter Email</div>
    <div class="nl-btn">SUBSCRIBE</div>
    <p class="copy">© Copyright 2022 Bruno Lessway Films Ltd.<br>All Rights Reserved</p>
  </div>
</footer>

</body>
</html>
```